Velmora Systems Website

Website design for our company: Velmora Systems.
The website should look fresh and IT focused. Please have a look at http://www.velmorasystems.example.au/ for our current design. We want something fresh and new, professional looking, in WordPress so we can easily make changes.

It Company

```html
<!DOCTYPE html>
<html lang="en">
<head>
<meta charset="utf-8">
<title>Velmora Systems</title>
<link href="https://fonts.googleapis.com/css2?family=Open+Sans:wght@300;400;600&display=swap" rel="stylesheet">
<style>
:root{
  --green:#00b15a;
  --green-accent:#1fbf6c;
  --sky:#cfe3ec;
  --white:#ffffff;
  --blue-text:#1b72bf;
  --body-text:#6a6a6a;
  --muted:#9a9a9a;
  --rule:#e3e3e3;
  --footer-top:#3e3e3e;
  --footer-bottom:#2a2a2a;
  --footer-text:#c9c9c9;
  --base:#1c1c1c;
  --field:#1f1f1f;
}
*{margin:0;padding:0;box-sizing:border-box}
html,body{width:1062px;height:1200px;overflow:hidden}
body{position:relative;background:var(--sky);font-family:"Open Sans",Arial,sans-serif;color:var(--body-text)}
.site-header{position:absolute;left:0;top:0;width:1062px;height:92px;background:var(--green)}
.brand{position:absolute;left:88px;top:28px;display:flex;align-items:center;gap:8px;color:var(--white);font-weight:600;font-size:17px}
.brand-dot{width:22px;height:22px;border-radius:50%;background:var(--white)}
.search{position:absolute;left:807px;top:16px;width:166px;height:28px;background:var(--white);border-radius:2px;font-size:12px;color:#aaa;padding:6px 8px}
.search svg{position:absolute;right:6px;top:5px}
.search::after{content:"";position:absolute;right:28px;top:4px;width:1px;height:20px;background:#ddd}
.main-nav{position:absolute;top:63px;left:0;font-size:13px;font-weight:600;color:var(--white)}
.main-nav span{position:absolute;white-space:nowrap}
.nav-active{position:absolute;left:359px;top:84px;width:51px;height:8px;background:var(--white);border-radius:3px 3px 0 0}
.page{position:absolute;left:88px;top:92px;width:886px;height:828px;background:var(--white)}
.hero{position:absolute;left:97px;top:104px;width:867px;height:351px;overflow:hidden;background:radial-gradient(circle at 48% 40%,#7fe6f2 0%,#2ab0d8 25%,#1466b0 55%,#0b2a6e 85%)}
.hero-arrow{position:absolute;top:135px;width:40px;height:80px;background:var(--white);border-radius:50%}
.hero-chevron{position:absolute;top:168px}
.hero-caption{position:absolute;right:30px;top:273px;text-align:right;color:var(--white);font-size:22px;line-height:28px}
.intro-lead{position:absolute;left:88px;top:483px;width:886px;text-align:center;color:var(--blue-text);font-size:13px;white-space:nowrap}
.intro-body{position:absolute;left:130px;top:510px;width:800px;text-align:center;font-size:12.5px;line-height:20.3px}
.rule{position:absolute;left:97px;width:868px;height:1px;background:var(--rule)}
.feature{position:absolute;top:645px;width:290px;height:84px}
.feature-ring{position:absolute;left:0;top:0;width:83px;height:83px;border:2px solid var(--green-accent);border-radius:50%;display:flex;align-items:center;justify-content:center}
.feature h3{position:absolute;left:91px;top:-2px;font-weight:400;font-size:24px;color:var(--green-accent);white-space:nowrap}
.feature p{position:absolute;left:92px;top:31px;width:170px;font-size:11.5px;line-height:15px;color:var(--muted)}
.testimonial{position:absolute;left:97px;top:793px;width:867px;text-align:center;font-size:15.7px;line-height:22px;color:#555}
.quote-mark{font-size:16px;font-weight:600;color:#555}
.testimonial cite{display:block;margin-top:8px;font-style:normal;font-size:13.5px;color:var(--blue-text)}
.site-footer{position:absolute;left:88px;top:920px;width:886px;height:227px;background:linear-gradient(var(--footer-top),var(--footer-bottom))}
.footer-heading{position:absolute;top:30px;color:var(--white);font-size:14px;font-weight:400}
.footer-list{position:absolute;top:63px;list-style:none;font-size:11.8px;line-height:22px;color:var(--footer-text)}
.social{position:absolute;left:20px;top:172px;display:flex;gap:5px}
.social span{width:25px;height:25px;background:#e6e6e6;border-radius:2px}
.field{position:absolute;left:599px;width:204px;background:var(--field);border-radius:2px;font-size:11.5px;color:#777;padding:9px 11px}
.submit{position:absolute;left:811px;top:170px;width:57px;height:28px;background:#555;border-radius:2px;color:var(--white);font-size:11.5px;text-align:center;line-height:28px}
.base-bar{position:absolute;left:0;top:1147px;width:1062px;height:53px;background:var(--base);text-align:center;color:#aaa;font-size:11.8px;line-height:53px}
</style>
</head>
<body>
<header class="site-header">
  <div class="brand"><span class="brand-dot"></span>Velmora Systems</div>
  <div class="search">Search
    <svg width="16" height="16" viewBox="0 0 16 16"><circle cx="6.5" cy="6.5" r="4.5" fill="none" stroke="#999" stroke-width="2"/><line x1="10" y1="10" x2="14" y2="14" stroke="#999" stroke-width="2.4"/></svg>
  </div>
  <nav class="main-nav">
    <span style="left:365px">HOME</span>
    <span style="left:430px">ABOUT US</span>
    <span style="left:522px">CLIENTS</span>
    <span style="left:599px">SERVICES</span>
    <span style="left:683px">SUPPORTS</span>
    <span style="left:776px">TESTIMONIALS</span>
    <span style="left:895px">CONTACT US</span>
  </nav>
  <div class="nav-active"></div>
</header>

<main class="page"></main>

<section class="hero" role="img" aria-label="Hand touching a glowing cloud over a blue bokeh background">
  <div class="hero-arrow" style="left:-20px"></div>
  <div class="hero-arrow" style="right:-20px"></div>
  <svg class="hero-chevron" style="left:3px" width="10" height="14" viewBox="0 0 10 14"><path d="M8 2 3 7l5 5" fill="none" stroke="#333" stroke-width="2.4"/></svg>
  <svg class="hero-chevron" style="right:3px" width="10" height="14" viewBox="0 0 10 14"><path d="M2 2l5 5-5 5" fill="none" stroke="#333" stroke-width="2.4"/></svg>
  <div class="hero-caption">FOR YOUR<br>NETWORK RELATED SERVICES</div>
</section>

<p class="intro-lead">Velmora Systems is an Adelaide based company with a single objective - to excel in the support and service of all computer and IT needs.</p>
<p class="intro-body">We provide a high level of consulting services using the most experienced engineers at a reasonable and fair price. We believe in using a Business Value approach to every aspect of computer consulting to provide our clients with the most cost effective solutions. We strongly believe that we are in business with our clients. Each thing we do must be measured against our clients’ business objectives. At the end of the day our client's success is our success.</p>

<div class="rule" style="top:619px"></div>

<section class="feature" style="left:112px">
  <div class="feature-ring">
    <svg width="26" height="26" viewBox="0 0 26 26" fill="var(--green-accent)"><circle cx="13" cy="13" r="9" fill="none" stroke="var(--green-accent)" stroke-width="2" stroke-dasharray="4 3"/><rect x="10" y="1" width="6" height="6"/><rect x="10" y="19" width="6" height="6"/><rect x="1" y="10" width="6" height="6"/><rect x="19" y="10" width="6" height="6"/></svg>
  </div>
  <h3>Network Services</h3>
  <p>Aliquam ultricies, sapien vel molestie placerat, dolor ligula suscipit leo, sit amet.</p>
</section>
<section class="feature" style="left:418px">
  <div class="feature-ring">
    <svg width="24" height="26" viewBox="0 0 24 26" fill="var(--green-accent)"><ellipse cx="12" cy="4" rx="11" ry="4"/><path d="M1 7c0 2 5 4 11 4s11-2 11-4v4c0 2-5 4-11 4S1 13 1 11z"/><path d="M1 14c0 2 5 4 11 4s11-2 11-4v4c0 2-5 4-11 4S1 20 1 18z"/></svg>
  </div>
  <h3>Servers</h3>
  <p>Aliquam ultricies, sapien vel molestie placerat, dolor ligula suscipit leo, sit amet.</p>
</section>
<section class="feature" style="left:707px">
  <div class="feature-ring">
    <svg width="22" height="26" viewBox="0 0 22 26"><path d="M11 1 21 4v8c0 7-5 11-10 13C6 23 1 19 1 12V4z" fill="var(--green-accent)"/></svg>
  </div>
  <h3>Security</h3>
  <p>Aliquam ultricies, sapien vel molestie placerat, dolor ligula suscipit leo, sit amet.</p>
</section>

<div class="rule" style="top:758px"></div>

<blockquote class="testimonial">
  <span class="quote-mark">&ldquo;</span>&nbsp; I have always found the team extremely helpful with their advice over the phone.<br>
  They also have the ability to access our computers remotely, and can rectify most problems quite swiftly.<br>
  I have no hesitation in recommending Velmora Systems for all of your IT needs. &nbsp;<span class="quote-mark">&rdquo;</span>
  <cite>- &nbsp;Daniel Hartwell B.Pharm, Northgate Pharmacy, Kelby Vale</cite>
</blockquote>

<footer class="site-footer">
  <h4 class="footer-heading" style="left:19px">Navigation Menu</h4>
  <ul class="footer-list" style="left:19px"><li>Home</li><li>About us</li><li>Clients</li><li>Services</li></ul>
  <ul class="footer-list" style="left:112px"><li>Support</li><li>Testimonials</li><li>Contact us</li></ul>
  <h4 class="footer-heading" style="left:260px">Our Services</h4>
  <ul class="footer-list" style="left:260px"><li>On-site Service</li><li>Remote Desktop Support</li><li>Medical IT Service</li><li>Pharmacy IT Service</li></ul>
  <ul class="footer-list" style="left:418px"><li>Website Design</li><li>Disaster Recovery</li><li>Hardware/ Software supply</li><li>Consumables</li></ul>
  <div class="social"><span></span><span></span><span></span><span></span><span></span></div>
  <h4 class="footer-heading" style="left:602px">Contact us</h4>
  <div class="field" style="top:66px;height:31px">Name</div>
  <div class="field" style="top:103px;height:31px">E-mail</div>
  <div class="field" style="top:140px;height:59px">Comment</div>
  <div class="submit">SUBMIT</div>
</footer>

<div class="base-bar">Copyright &nbsp;© 2014 &nbsp;Velmora Systems . &nbsp; All rights reserved.</div>
</body>
</html>
```